The Plate Compass

Cutting Through the Noise to What Actually Works.

Nutrition book

Target Market(s)

People looking to be or get healthy and eat right.

```html
<!DOCTYPE html>
<html lang="en">
<head>
<meta charset="utf-8">
<title>The Plate Compass</title>
<link rel="stylesheet" href="https://fonts.googleapis.com/css2?family=Anton&family=Libre+Baskerville:ital,wght@0,700;1,400&family=Barlow:wght@500&display=swap">
<style>
  :root {
    --paper: #f5ede2;
    --paper-deep: #ebe0d2;
    --title-dark: #0f2c1b;
    --title-olive: #4e6a14;
    --layer-calories: #1f5b27;
    --layer-protein: #7f911b;
    --layer-quality: #e2a713;
    --layer-timing: #d8700f;
    --layer-supplements: #b7916f;
    --layer-noise: #3a3a38;
    --label: #fbf5e8;
    --food-green: #4f7d34;
    --food-olive: #a7a83a;
    --food-wood: #7a4e2a;
    --food-bowl: #ddd3c5;
    --food-berry: #3d4f86;
    --food-almond: #a0683a;
  }
  * { margin: 0; padding: 0; box-sizing: border-box; }
  html, body { width: 800px; height: 1200px; overflow: hidden; }
  body { background: var(--paper); }
  .cover {
    position: relative;
    width: 800px; height: 1200px; overflow: hidden;
    background: radial-gradient(ellipse at 50% 40%, #f8f1e7 0%, var(--paper) 55%, var(--paper-deep) 100%);
  }
  .title {
    position: absolute; top: 58px; left: 0; width: 800px;
    text-align: center; font-family: "Anton", "Impact", sans-serif;
    text-transform: uppercase; line-height: 0.92;
  }
  .title-line { display: block; }
  .title-the { font-size: 112px; color: var(--title-dark); }
  .title-main { font-size: 150px; color: var(--title-dark); }
  .title-accent { font-size: 150px; color: var(--title-olive); }
  .subtitle {
    position: absolute; top: 484px; left: 0; width: 800px; text-align: center;
    font-family: "Libre Baskerville", Georgia, serif; font-style: italic; font-weight: 400;
    font-size: 19px; color: var(--title-dark);
  }
  .food-area { position: absolute; }
  .food-left {
    left: 0; top: 570px; width: 210px; height: 560px;
    border-radius: 0 120px 90px 0;
    background: linear-gradient(180deg, rgba(79,125,52,0) 0%, var(--food-green) 30%, var(--food-olive) 60%, var(--food-wood) 90%, rgba(122,78,42,0) 100%);
    opacity: 0.85;
  }
  .food-right {
    left: 615px; top: 830px; width: 185px; height: 330px;
    border-radius: 110px 0 0 90px;
    background: linear-gradient(180deg, rgba(79,125,52,0) 0%, var(--food-green) 20%, var(--food-bowl) 48%, var(--food-berry) 70%, var(--food-almond) 90%, rgba(160,104,58,0) 100%);
    opacity: 0.8;
  }
  .funnel { position: absolute; left: 0; top: 0; }
  .layer-label {
    font-family: "Libre Baskerville", Georgia, serif; font-weight: 700;
    fill: var(--label);
  }
  .layer-icon { fill: none; stroke: var(--label); stroke-width: 2; stroke-linecap: round; stroke-linejoin: round; }
  .author {
    position: absolute; top: 1120px; left: 0; width: 800px; text-align: center;
    font-family: "Barlow", "Arial", sans-serif; font-weight: 500;
    font-size: 36px; letter-spacing: 4px; color: var(--title-olive);
  }
</style>
</head>
<body>
<main class="cover">
  <div class="food-area food-left" role="img" aria-label="Halved avocado on a wooden board with leafy greens and spinach"></div>
  <div class="food-area food-right" role="img" aria-label="Bowl of blueberries with loose berries, almonds and greens"></div>

  <h1 class="title">
    <span class="title-line title-the">The</span>
    <span class="title-line title-main">Plate</span>
    <span class="title-line title-accent">Compass</span>
  </h1>
  <p class="subtitle">Cutting Through the Noise to What Actually Works.</p>

  <svg class="funnel" width="800" height="1200" viewBox="0 0 800 1200" aria-label="Priority funnel">
    <defs>
      <filter id="layer-shadow" x="-10%" y="-20%" width="120%" height="160%">
        <feDropShadow dx="0" dy="5" stdDeviation="5" flood-color="#3b2a18" flood-opacity="0.3"/>
      </filter>
    </defs>

    <g class="layer layer-noise" filter="url(#layer-shadow)">
      <path d="M291 934 L316 1015 A82 10 0 0 0 480 1015 L505 934 Z" fill="var(--layer-noise)"/>
      <ellipse cx="398" cy="934" rx="107" ry="9" fill="#4a4a47"/>
    </g>
    <g class="layer layer-supplements" filter="url(#layer-shadow)">
      <path d="M260 863 L288 932 A111 10 0 0 0 510 932 L538 863 Z" fill="var(--layer-supplements)"/>
      <ellipse cx="399" cy="863" rx="139" ry="9" fill="#c7a587"/>
    </g>
    <g class="layer layer-timing" filter="url(#layer-shadow)">
      <path d="M227 792 L260 859 A140 10 0 0 0 541 859 L571 792 Z" fill="var(--layer-timing)"/>
      <ellipse cx="399" cy="792" rx="172" ry="10" fill="#e6843a"/>
    </g>
    <g class="layer layer-quality" filter="url(#layer-shadow)">
      <path d="M191 718 L224 787 A178 11 0 0 0 581 787 L605 718 Z" fill="var(--layer-quality)"/>
      <ellipse cx="398" cy="718" rx="207" ry="11" fill="#efc24a"/>
    </g>
    <g class="layer layer-protein" filter="url(#layer-shadow)">
      <path d="M156 641 L194 713 A208 12 0 0 0 610 713 L643 641 Z" fill="var(--layer-protein)"/>
      <ellipse cx="400" cy="641" rx="244" ry="12" fill="#95a532"/>
    </g>
    <g class="layer layer-calories" filter="url(#layer-shadow)">
      <path d="M112 551 L148 630 A255 13 0 0 0 658 630 L687 551 Z" fill="var(--layer-calories)"/>
      <ellipse cx="400" cy="551" rx="288" ry="12" fill="#2b6e33"/>
    </g>

    <g class="layer-icon" transform="translate(292 603)">
      <path d="M0 -10 C-10 -16 -22 -8 -20 6 C-18 18 -8 24 0 20 C8 24 18 18 20 6 C22 -8 10 -16 0 -10 Z"/>
      <path d="M0 -10 L2 -20"/><path d="M3 -17 C8 -22 14 -20 14 -20 C12 -15 7 -14 3 -17 Z"/>
    </g>
    <text class="layer-label" x="415" y="613" font-size="30" text-anchor="middle">Calories</text>

    <g class="layer-icon" transform="translate(291 686)">
      <rect x="-17" y="-11" width="6" height="22" rx="1"/><rect x="-23" y="-7" width="6" height="14" rx="1"/>
      <rect x="11" y="-11" width="6" height="22" rx="1"/><rect x="17" y="-7" width="6" height="14" rx="1"/>
      <path d="M-11 0 L11 0"/>
    </g>
    <text class="layer-label" x="412" y="696" font-size="26" text-anchor="middle">Protein</text>

    <g class="layer-icon" transform="translate(301 763)">
      <path d="M-14 14 C-18 -6 -4 -16 16 -16 C16 4 6 16 -14 14 Z"/>
      <path d="M-18 18 L8 -8"/>
    </g>
    <text class="layer-label" x="425" y="772" font-size="22" text-anchor="middle">Food Quality</text>

    <g class="layer-icon" transform="translate(311 834)">
      <circle r="17"/><path d="M0 -9 L0 0 L7 6"/>
    </g>
    <text class="layer-label" x="428" y="843" font-size="21" text-anchor="middle">Meal Timing</text>

    <g class="layer-icon" transform="translate(321 904) rotate(-45)">
      <rect x="-17" y="-8" width="34" height="16" rx="8"/><path d="M0 -8 L0 8"/>
    </g>
    <text class="layer-label" x="426" y="913" font-size="20" text-anchor="middle">Supplements</text>

    <g class="layer-icon" transform="translate(354 980)">
      <path d="M-14 -5 L4 -14 L4 14 L-14 5 Z"/><path d="M-18 -5 L-14 -5 L-14 5 L-18 5 Z"/>
      <path d="M-12 6 L-9 16 L-4 16 L-7 7"/><path d="M8 -4 C11 -2 11 2 8 4"/>
    </g>
    <text class="layer-label" x="424" y="990" font-size="21" text-anchor="middle">Noise</text>
  </svg>

  <p class="author">AUTHOR’S NAME</p>
</main>
</body>
</html>
```